Veltrano.co - Polar Expeditions Specialists

We need a modern, visually striking business card for Veltrano.co, a company specialized in selling expedition cruises to the most remote regions on Earth, with a focus on the Arctic and Antarctica. The design should instantly communicate that the cardholder is an expert in polar travel. Use clean, premium aesthetics with cool tones like icy blue and white, possibly incorporating polar imagery (ice, glaciers, penguins, etc.)

Attached the logo

Contact Information for Business Card

Feels high-end and trustworthy.. Visually memorable — encourages people to keep it

Colors
0054AA
0677BA
7BADD7
CADEEF
E8F1F8

Requirements
Must have
• ice, glaciers, penguins, montains
Nice to have
• modern, transparente,

```html
<!DOCTYPE html>
<html lang="en">
<head>
<meta charset="utf-8">
<title>Veltrano.co – Business Card</title>
<link href="https://fonts.googleapis.com/css2?family=Poppins:wght@400;500;700;800&display=swap" rel="stylesheet">
<style>
  :root {
    --bg: #e6e9ee;
    --card-white: #ffffff;
    --card-navy: #12122b;
    --brand-blue: #3174b8;
    --text-light: #f2f4f8;
    --shadow: rgba(10, 20, 40, 0.25);
  }
  * { box-sizing: border-box; margin: 0; padding: 0; }
  html, body { width: 1200px; height: 900px; overflow: hidden; }
  body {
    background: var(--bg);
    font-family: "Poppins", sans-serif;
    display: flex;
    flex-direction: column;
    align-items: center;
    justify-content: center;
    gap: 56px;
  }
  .card {
    width: 595px;
    height: 340px;
    border-radius: 22px;
    position: relative;
    overflow: hidden;
    box-shadow: 0 14px 30px var(--shadow);
  }

  /* Front */
  .card-front {
    background: var(--card-white);
    display: flex;
    flex-direction: column;
    align-items: center;
    justify-content: center;
    color: var(--brand-blue);
  }
  .front-mark {
    width: 22px; height: 22px; border-radius: 50%;
    background: var(--brand-blue);
    margin-bottom: 18px;
  }
  .front-name {
    font-weight: 800;
    font-size: 74px;
    line-height: 1;
    letter-spacing: 0.5px;
  }
  .front-tagline {
    font-weight: 700;
    font-size: 22px;
    margin-top: 8px;
  }

  /* Back */
  .card-back {
    background: var(--card-navy);
    color: var(--text-light);
  }
  .back-illustration {
    position: absolute;
    left: 0; top: 0;
    width: 290px; height: 340px;
  }
  .back-content {
    position: absolute;
    left: 290px; top: 44px;
    right: 28px;
  }
  .back-logo {
    display: flex;
    align-items: center;
    gap: 10px;
    color: var(--brand-blue);
  }
  .back-logo-mark {
    width: 14px; height: 14px; border-radius: 50%;
    background: var(--brand-blue);
  }
  .back-logo-name {
    font-weight: 800;
    font-size: 36px;
    line-height: 1;
  }
  .back-tagline {
    color: var(--brand-blue);
    font-weight: 700;
    font-size: 11.5px;
    margin: 4px 0 0 24px;
  }
  .holder-name {
    margin-top: 22px;
    color: var(--brand-blue);
    font-weight: 700;
    font-size: 24px;
    line-height: 1.1;
  }
  .holder-role {
    font-size: 13px;
    margin-top: 2px;
  }
  .address {
    font-size: 13px;
    line-height: 1.35;
    margin-top: 14px;
  }
  .contact-list {
    list-style: none;
    margin-top: 12px;
    font-size: 13px;
    line-height: 1.5;
  }
  .contact-list li { display: flex; align-items: center; gap: 8px; }
  .contact-icon { width: 11px; height: 11px; fill: var(--text-light); flex: none; }
</style>
</head>
<body>

  <section class="card card-front">
    <div class="front-mark"></div>
    <h1 class="front-name">Veltrano.co</h1>
    <p class="front-tagline">Polar Expeditions Specialists</p>
  </section>

  <section class="card card-back">
    <svg class="back-illustration" viewBox="0 0 290 340" role="img" aria-label="Large blue silhouette of a polar bear standing over two penguins">
      <path d="M0 340 L0 150 C30 80 90 40 170 40 C230 40 265 70 265 120 C265 200 275 270 290 340 Z" fill="#3174b8"/>
    </svg>

    <div class="back-content">
      <div class="back-logo">
        <span class="back-logo-mark"></span>
        <span class="back-logo-name">Veltrano.co</span>
      </div>
      <p class="back-tagline">Polar Expeditions Specialists</p>

      <h2 class="holder-name">Marlon Quist</h2>
      <p class="holder-role">CEO &amp; Founder</p>

      <p class="address">42 Harbor Crest Lane,<br>Lakeview, ME 04112 USA</p>

      <ul class="contact-list">
        <li>
          <svg class="contact-icon" viewBox="0 0 12 12"><path d="M2 1h3l1 3-2 1c1 2 2 3 3 3l1-2 3 1v3c-6 0-9-3-9-9z"/></svg>
          +1.555.014.273
        </li>
        <li>
          <svg class="contact-icon" viewBox="0 0 12 12"><path d="M0 2h12v8H0z M0 2l6 4 6-4" /></svg>
          hello@veltranomail.com
        </li>
        <li>
          <svg class="contact-icon" viewBox="0 0 12 12"><circle cx="6" cy="6" r="6"/></svg>
          www.veltranotrips.com
        </li>
      </ul>
    </div>
  </section>

</body>
</html>
```